showcase project portfolio

create power point of project portfolio
from word file and website using similar design template

https://www.brelmor.co.uk/

Target Market(s)

corporte

```html
<!DOCTYPE html>
<html lang="en">
<head>
<meta charset="utf-8">
<title>Brelmor – Project Portfolio</title>
<link href="https://fonts.googleapis.com/css2?family=Raleway:wght@400;500;600;700&family=Montserrat:wght@700&display=swap" rel="stylesheet">
<style>
:root{
  --board:#4d4d4d;
  --paper:#ffffff;
  --navy:#1c3d54;
  --sand:#c9a488;
  --sand-panel:#c8a184;
  --ink:#2b2b2b;
  --muted:#555;
}
*{box-sizing:border-box;margin:0;padding:0}
html,body{width:1019px;height:1200px;overflow:hidden;background:var(--board)}
body{position:relative;font-family:"Raleway",sans-serif;color:var(--ink)}
.slide{position:absolute;width:478px;height:269px;background:var(--paper);overflow:hidden}
.col-left{left:18px}.col-right{left:521px}
.row-1{top:16px}.row-2{top:311px}.row-3{top:611px}.row-4{top:910px}
.abs{position:absolute}
.wordmark{position:absolute;font-family:"Raleway",sans-serif;font-weight:700;letter-spacing:.12em;color:var(--navy);font-size:7px;white-space:nowrap}
.wordmark.corner{right:10px;top:14px;text-align:right}
.wordmark.light{color:#fff}
.photo{position:absolute;box-shadow:0 1px 3px rgba(0,0,0,.25)}
.ph-brick{background:linear-gradient(160deg,#8a5a48,#6e4a3d 55%,#585c5c)}
.ph-street{background:linear-gradient(180deg,#b9c3cb,#7a6e62 55%,#5a5a58)}
.ph-green{background:linear-gradient(180deg,#6d8a4a,#3f5a2c)}
.ph-house{background:linear-gradient(180deg,#c6d1d8,#5e5450 55%,#6a6866)}
.ph-plan{background:linear-gradient(180deg,#f6f6ef,#eef0d2);border:1px solid #ddd}
.ph-plan-grey{background:linear-gradient(180deg,#fafafa,#ececec);border:1px solid #ddd}
.proj-title{position:absolute;left:22px;color:var(--sand);font-weight:700;font-size:8.6px;letter-spacing:.06em}
.meta{position:absolute;left:22px;font-size:8px;line-height:13.3px}
.meta dt{position:absolute;left:0;color:var(--ink);font-weight:500}
.meta dd{margin-left:48px;color:var(--muted);text-align:justify}
.meta .gap{height:7px}
/* cover */
.cover{background:linear-gradient(135deg,#fbfbfb,#f1f2f3)}
.cover .headline{position:absolute;left:27px;top:142px;font-size:21.5px;line-height:29px;color:var(--navy);font-weight:500}
.cover .headline .accent{color:var(--sand)}
.cover .wordmark.small{left:27px;top:120px;font-size:6px}
.cover .wordmark.large{left:250px;top:120px;font-size:26px;letter-spacing:.1em}
/* tasks */
.tasks .hero{left:0;top:0;width:211px;height:269px;background:linear-gradient(180deg,#b8c5cf 0%,#7d5543 45%,#6e7c86 100%)}
.tasks .panel{position:absolute;left:211px;top:0;width:267px;height:269px;background:var(--sand-panel)}
.tasks h2{position:absolute;left:14px;top:26px;font-size:18px;font-weight:700;color:#fff;letter-spacing:.04em}
.tasks ul{position:absolute;left:14px;top:54px;list-style:none;color:#fff;font-size:7.4px;line-height:13.45px;width:252px}
.tasks li{padding-left:9px;position:relative}
.tasks li::before{content:"";position:absolute;left:0;top:6px;width:2px;height:2px;background:#fff;border-radius:50%}
/* project one */
.p1-heading{position:absolute;left:22px;top:52px;font-size:11.5px;line-height:19px;font-weight:700;color:var(--ink)}
/* thank you */
.closing{background:linear-gradient(160deg,#2d4f68,#1f3f57 60%,#25455d)}
.closing .wordmark{left:0;right:0;text-align:center;top:118px;font-size:12px}
.closing h2{position:absolute;left:0;right:0;top:140px;text-align:center;font-family:"Montserrat",sans-serif;font-weight:700;font-size:34px;color:#fff}
</style>
</head>
<body>

<section class="slide col-left row-1 cover">
  <span class="wordmark small">BRELMOR</span>
  <h1 class="headline"><span class="accent">Architecture</span> today<br>Ready for tomorrow</h1>
  <span class="wordmark large">BRELMOR</span>
</section>

<section class="slide col-right row-1">
  <span class="wordmark corner">BRELMOR</span>
  <h2 class="proj-title" style="top:62px">PROJECT THREE</h2>
  <dl class="meta" style="top:92px;width:196px">
    <dt>Location :</dt><dd>41-45 Calder Row Derby</dd>
    <div class="gap"></div>
    <dt>Proposal :</dt><dd>Refurbishment Of Commercial Ground Floor Units Together With Formation Of 6 Residential Units On First And Second Floors. Installation Of Glazing And Repair To External Masonry Including Bricking Up Of Existing Openings</dd>
  </dl>
  <div class="photo ph-street" style="left:229px;top:65px;width:114px;height:79px" role="img" aria-label="Street photo of the commercial building"></div>
  <div class="photo ph-street" style="left:360px;top:65px;width:92px;height:76px" role="img" aria-label="Side view of the building along the street"></div>
  <div class="photo ph-plan" style="left:229px;top:159px;width:224px;height:90px" role="img" aria-label="Floor plans of the ground, first and second floors"></div>
</section>

<section class="slide col-left row-2 tasks">
  <div class="photo hero" role="img" aria-label="Rendering of a brick house with tall glazed gables"></div>
  <div class="panel">
    <span class="wordmark corner light">BRELMOR</span>
    <h2>TASKS</h2>
    <ul>
      <li>Creating working drawings</li>
      <li>Price breakdown of total build costs</li>
      <li>Liaising with Midvale Waters for water connection, drainage connection</li>
      <li>Liaising with Northline Gas to get gas supply to site</li>
      <li>Liaising with Unity Power Network to get electric supply</li>
      <li>Tendering out works to different tradesman</li>
      <li>Getting material orders</li>
      <li>Arranging structural engineer for the site</li>
      <li>Arranging Building control for the site</li>
      <li>Making sure material is on site on time</li>
      <li>Making sure all tradesman work is up to current British standards</li>
      <li>Daily walk rounds to check work is done according to approved plans</li>
      <li>Placing orders for bathrooms, kitchen, and flooring</li>
      <li>All snag work with main contactor</li>
    </ul>
  </div>
</section>

<section class="slide col-right row-2">
  <span class="wordmark corner">BRELMOR</span>
  <h2 class="proj-title" style="top:62px">PROJECT FOUR</h2>
  <dl class="meta" style="top:92px;width:196px">
    <dt>Location :</dt><dd style="white-space:nowrap">Land At 7 Hollybank Derby DE21 4QX</dd>
    <div class="gap"></div>
    <dt>Proposal :</dt><dd>Erection of a dwelling house (use class C3)</dd>
  </dl>
  <div class="photo ph-green" style="left:229px;top:65px;width:114px;height:80px" role="img" aria-label="Overgrown plot before construction"></div>
  <div class="photo ph-house" style="left:360px;top:66px;width:92px;height:76px" role="img" aria-label="Completed detached house"></div>
  <div class="photo ph-plan-grey" style="left:179px;top:159px;width:118px;height:94px" role="img" aria-label="Floor plans and site plan"></div>
  <div class="photo ph-plan-grey" style="left:315px;top:163px;width:139px;height:81px" role="img" aria-label="Proposed front elevation drawing"></div>
</section>

<section class="slide col-left row-3">
  <span class="wordmark corner">BRELMOR</span>
  <h2 class="proj-title" style="top:36px">PROJECT ONE</h2>
  <p class="p1-heading">Garages at Ashcombe Mews,<br>Ashcombe Street, Derby</p>
  <dl class="meta" style="top:112px;width:192px">
    <dt>Proposal :</dt><dd>Change of use from garages to two dwelling houses (use class C3) including alterations to the front and side elevations</dd>
  </dl>
  <div class="photo ph-plan" style="left:239px;top:63px;width:97px;height:81px" role="img" aria-label="Plans and elevations of the garage conversion"></div>
  <div class="photo ph-brick" style="left:362px;top:66px;width:92px;height:75px" role="img" aria-label="Converted brick mews houses"></div>
  <div class="photo ph-brick" style="left:293px;top:165px;width:113px;height:86px" role="img" aria-label="Original brick garages along the lane"></div>
</section>

<section class="slide col-right row-3">
  <span class="wordmark corner">BRELMOR</span>
  <h2 class="proj-title" style="top:38px">PROJECT FIVE</h2>
  <dl class="meta" style="top:68px;width:180px">
    <dt>Location :</dt><dd>16, Larkfield Street, Birmingham</dd>
    <div class="gap"></div>
    <dt>Proposal :</dt><dd>Warehouse conversion to 4 town houses.</dd>
  </dl>
  <div class="photo ph-brick" style="left:217px;top:23px;width:95px;height:107px" role="img" aria-label="Warehouse frontage before conversion"></div>
  <div class="photo ph-brick" style="left:338px;top:25px;width:81px;height:105px" role="img" aria-label="Warehouse frontage after conversion"></div>
  <div class="photo ph-plan-grey" style="left:217px;top:156px;width:94px;height:72px" role="img" aria-label="Floor plans of the town houses"></div>
  <div class="photo ph-brick" style="left:342px;top:149px;width:73px;height:97px" role="img" aria-label="Rear courtyard of the warehouse"></div>
</section>

<section class="slide col-left row-4">
  <span class="wordmark corner">BRELMOR</span>
  <h2 class="proj-title" style="top:62px">PROJECT TWO</h2>
  <dl class="meta" style="top:92px;width:192px">
    <dt>Location :</dt><dd>218 Fernleigh Road, Derby</dd>
    <div class="gap"></div>
    <dt>Proposal :</dt><dd style="text-align:left">Change of use from offices (use class B1) to 12 flats (use class C3)</dd>
  </dl>
  <div class="photo ph-plan-grey" style="left:230px;top:64px;width:114px;height:80px" role="img" aria-label="Floor plans for the flats"></div>
  <div class="photo ph-brick" style="left:362px;top:66px;width:92px;height:75px" role="img" aria-label="Brick office building front"></div>
  <div class="photo ph-brick" style="left:293px;top:165px;width:113px;height:86px" role="img" aria-label="Building viewed from the road"></div>
</section>

<section class="slide col-right row-4 closing" role="img" aria-label="Closing slide over a street scene">
  <span class="wordmark light">BRELMOR</span>
  <h2>Thank You</h2>
</section>

</body>
</html>
```